Boutique custom software development company needs new business card

Our nearly 20 year old custom software development company would like to better include the fact that we are now providing Bitcoin services. These new services are B2B include education (how to acquire and securely hold Bitcoin) and integrating Bitcoin payments into existing ecommerce sites or other existing systems. Please keep the card clean and simple. Attached is our current design and some other files. vextorial.com

Target Market(s)

businesses owners interested in long term relationship

Industry/Entity Type

Custom software development and Bitcoin

Contact Information for Business Card

Dale Parker, dale@vextorial.com, vextorial.com, (888) 555-VXTRL

Font styles to use
Other font styles liked:
• monospace

Requirements
Must have
• double-sided
Nice to have
• clean and simple
Should not have
• physical address

```html
<!DOCTYPE html>
<html lang="en">
<head>
<meta charset="utf-8">
<title>Vextorial Business Card</title>
<link rel="stylesheet" href="https://fonts.googleapis.com/css2?family=Poppins:wght@400;500;700;800&display=swap">
<style>
  :root {
    --backdrop: #3a3a3a;
    --card: #0a0a0a;
    --brand-blue: #3f74bd;
    --brand-orange: #f07c22;
    --ink-light: #f2f2f2;
    --ink-muted: #b8b8b8;
  }
  * { margin: 0; padding: 0; box-sizing: border-box; }
  html, body {
    width: 1200px;
    height: 1015px;
    overflow: hidden;
    background: var(--backdrop);
    font-family: "Poppins", sans-serif;
  }
  .sheet {
    width: 1200px;
    height: 1015px;
    display: flex;
    flex-direction: column;
    align-items: center;
    justify-content: center;
    gap: 40px;
  }
  .card {
    position: relative;
    width: 760px;
    height: 434px;
    background: var(--card);
    box-shadow: 0 12px 30px rgba(0,0,0,0.55);
    overflow: hidden;
  }

  /* Front */
  .card-front {
    display: flex;
    flex-direction: column;
    align-items: center;
    justify-content: center;
  }
  .wordmark {
    display: flex;
    align-items: center;
    gap: 16px;
  }
  .wordmark-square {
    width: 52px;
    height: 52px;
    background: var(--brand-orange);
  }
  .wordmark-name {
    font-weight: 800;
    font-size: 72px;
    line-height: 1;
    letter-spacing: 2px;
    text-transform: uppercase;
    color: var(--brand-blue);
  }
  .tagline {
    margin-top: 10px;
    font-weight: 400;
    font-size: 25px;
    color: var(--brand-blue);
    letter-spacing: 0.3px;
  }
  .service-line {
    margin-top: 14px;
    font-weight: 500;
    font-size: 17px;
    letter-spacing: 1.5px;
    text-transform: uppercase;
    color: var(--brand-orange);
  }

  /* Back */
  .holder-name {
    position: absolute;
    left: 70px;
    top: 110px;
    font-weight: 800;
    font-size: 34px;
    letter-spacing: 1px;
    text-transform: uppercase;
  }
  .holder-first { color: var(--brand-orange); }
  .holder-last { color: var(--brand-blue); }
  .holder-role {
    position: absolute;
    left: 70px;
    top: 162px;
    font-weight: 400;
    font-size: 17px;
    color: var(--ink-muted);
  }
  .contact-list {
    position: absolute;
    left: 70px;
    top: 250px;
    list-style: none;
  }
  .contact-item {
    display: flex;
    align-items: center;
    gap: 14px;
    height: 38px;
    margin-bottom: 6px;
    font-size: 22px;
    font-weight: 400;
    color: var(--ink-light);
  }
  .contact-icon {
    width: 32px;
    height: 32px;
    border-radius: 6px;
    background: var(--brand-orange);
    display: flex;
    align-items: center;
    justify-content: center;
  }
  .contact-icon svg { width: 20px; height: 20px; }
  .brand-block {
    position: absolute;
    right: 70px;
    top: 90px;
    width: 250px;
    height: 250px;
    background: var(--brand-blue);
  }
</style>
</head>
<body>
  <main class="sheet">
    <section class="card card-front">
      <div class="wordmark">
        <span class="wordmark-square"></span>
        <span class="wordmark-name">Vextorial</span>
      </div>
      <p class="tagline">developer of custom applications</p>
      <p class="service-line">Bitcoin education &amp; payment integration</p>
    </section>

    <section class="card card-back">
      <h1 class="holder-name"><span class="holder-first">Dale</span> <span class="holder-last">Parker</span></h1>
      <p class="holder-role">Custom Software &amp; Bitcoin Services</p>
      <ul class="contact-list">
        <li class="contact-item">
          <span class="contact-icon">
            <svg viewBox="0 0 24 24" fill="none" stroke="#fff" stroke-width="2" stroke-linecap="round" stroke-linejoin="round"><path d="M5 3h4l2 5-2.5 1.5a11 11 0 0 0 6 6L16 13l5 2v4a2 2 0 0 1-2 2A17 17 0 0 1 3 5a2 2 0 0 1 2-2z"/></svg>
          </span>
          (888) 555-VXTRL
        </li>
        <li class="contact-item">
          <span class="contact-icon">
            <svg viewBox="0 0 24 24" fill="none" stroke="#fff" stroke-width="2" stroke-linejoin="round"><rect x="3" y="5" width="18" height="14" rx="1"/><path d="M3 6l9 7 9-7"/></svg>
          </span>
          dale@vextorial.com
        </li>
        <li class="contact-item">
          <span class="contact-icon">
            <svg viewBox="0 0 24 24" fill="none" stroke="#fff" stroke-width="1.8"><circle cx="12" cy="12" r="9"/><ellipse cx="12" cy="12" rx="4" ry="9"/><path d="M3 12h18M5 7h14M5 17h14"/></svg>
          </span>
          www.vextorial.com
        </li>
      </ul>
      <div class="brand-block" aria-hidden="true"></div>
    </section>
  </main>
</body>
</html>
```